Nimbo31.com.au Website and company image design

We are looking for an exceptional website designer / company to work with our new Australian Hosting Company

Nimbo31 is a new Cloud Hosting company launching in Australia that provides Scalable, On Demand computing resources to the Australian Market Place. Scalable, On Demand ocmputing is a nice way of saying fully scalable / redundant Virtual Private Server.

We require a full company image to be developed along with a Logo and Website. There is scope for ongoing development (preferred) for the successful candidate.

Website developement will require extensive jQuery ability (sliders for ordering etc (see: http://www.hostrivo.com.au/virtual-dedicated-servers/253/kelp_vps.html).

Please communicate directly with me to establish full website scope and request further documentation / content.

Target Market(s)

Website Designers, programmers, technicians and large companies

Industry/Entity Type

It Company

Requirements
Must have
• Slider ordering system such as http://www.hostrivo.com.au/virtual-dedicated-servers/253/kelp_vps.html

Nice to have
• CMS backend system
Should not have
• Should NOT be a monster template copy!!!

```html
<!DOCTYPE html>
<html lang="en">
<head>
<meta charset="utf-8">
<title>Nimbo31 – Simple Cloud Hosting</title>
<link rel="stylesheet" href="https://fonts.googleapis.com/css2?family=Montserrat:wght@400;600;700&family=Open+Sans:wght@300;400;700&family=Arimo:wght@400;700&family=Tinos:ital@1&display=swap">
<style>
:root{
  --blue-dark:#1676c8;
  --blue:#2a92dc;
  --blue-sky:#8ccbf1;
  --blue-text:#14589c;
  --green:#79b530;
  --green-dark:#4f8d17;
  --red:#d81e1e;
  --red-dark:#b01010;
  --grey-bg:#f1f2f3;
  --grey-line:#d9dadc;
  --grey-btn:#e3e4e6;
  --text:#333;
  --text-soft:#555;
  --yellow:#f6c021;
}
*{box-sizing:border-box;margin:0;padding:0}
html,body{width:1200px;height:2286px;overflow:hidden;background:#fff}
body{font-family:"Arimo",Arial,sans-serif;color:var(--text)}
.page{position:relative;width:1200px;height:2286px;overflow:hidden;background:#fff}
.abs{position:absolute}

/* header */
.topbar{left:0;top:0;width:1200px;height:112px;background:linear-gradient(#1d86d6,#2a95e0)}
.brand{left:139px;top:14px;display:flex;align-items:center;gap:10px;font-family:"Montserrat",sans-serif;font-weight:700;font-size:40px;color:#fff}
.brand-dot{width:16px;height:16px;border-radius:50%;background:#fff}
.utility{left:584px;top:30px;width:292px;font-size:11px;color:#fff;display:flex;align-items:center;gap:6px;white-space:nowrap}
.utility .phone{font-family:"Montserrat",sans-serif;font-weight:600;font-size:15px;margin-left:8px}
.btn-signup{left:886px;top:18px;width:78px;height:42px;border-radius:5px;background:var(--yellow);border:1px solid #d49a00;font-family:"Montserrat",sans-serif;font-weight:600;font-size:15px;color:#333;display:flex;align-items:center;justify-content:center}
.btn-login{left:974px;top:18px;width:84px;height:42px;border-radius:5px;background:linear-gradient(#fff,#dcdcdc);border:1px solid #aaa;font-family:"Montserrat",sans-serif;font-weight:600;font-size:15px;color:#333;display:flex;align-items:center;justify-content:center;gap:7px}
.nav{left:156px;top:78px;width:890px;display:flex;justify-content:space-between;font-family:"Montserrat",sans-serif;font-size:16px;color:#fff}

/* hero */
.hero{left:0;top:112px;width:1200px;height:460px;background:linear-gradient(#3aa0e4,var(--blue-sky) 80%,#b6def6)}
.hero-title{left:0;top:146px;width:1200px;text-align:center;font-family:"Open Sans",sans-serif;font-weight:300;font-size:58px;line-height:70px;color:#fff}
.hero-sub{left:0;top:222px;width:1200px;text-align:center;font-family:"Arimo",sans-serif;font-weight:700;font-size:29px;line-height:34px;color:var(--blue-text)}
.hero-clouds{left:0;top:400px;width:1200px;height:172px;background:linear-gradient(rgba(255,255,255,0),#fff 65%)}
.hero-servers{left:695px;top:270px;width:286px;height:290px;border-radius:40px 40px 60px 60px;background:linear-gradient(#5b5f66,#c8ccd2 60%,#eef0f3)}

/* domain search */
.search{left:0;top:572px;width:1200px;height:70px;background:linear-gradient(#f4f4f4,#e2e3e5);border-bottom:1px solid #cfd0d2}
.search-label{left:156px;top:594px;font-family:"Montserrat",sans-serif;font-size:20px;color:#4a6c8c}
.search-input{left:398px;top:587px;width:400px;height:38px;background:#fff;border:1px solid #c9cbce;border-right:none;padding-left:12px;font-size:15px;line-height:36px;color:#888}
.search-tld{left:798px;top:587px;width:97px;height:38px;background:#fff;border:1px solid #c9cbce;font-size:13px;line-height:36px;padding-left:10px;color:#555}
.search-btn{left:910px;top:587px;width:130px;height:38px;border-radius:5px;background:linear-gradient(#3ba7ea,#1a7ccf);color:#fff;font-family:"Montserrat",sans-serif;font-weight:600;font-size:13px;display:flex;align-items:center;justify-content:center}

/* main */
.main{left:143px;top:657px;width:916px;height:1238px;background:var(--grey-bg);border:1px solid #e4e5e7}
.sidebox{background:#fff;border:1px solid var(--grey-line);border-radius:3px}
.aus{left:156px;top:674px;width:160px;height:378px}
.aus h3,.spam h3{font-family:"Montserrat",sans-serif;font-size:16px;text-align:center;margin-top:14px}
.aus h3{color:#222}
.aus-map{margin:8px auto 0;width:120px;height:84px;border-radius:10px;background:linear-gradient(135deg,#c8242b,#1d3f8f)}
.perk{margin:10px auto 0;width:142px;height:48px;border-radius:4px;background:linear-gradient(#f2f2f2,#d9dadc);border:1px solid #c6c7c9;font-size:11px;color:#333;text-align:center;display:flex;align-items:center;justify-content:center;padding:0 6px;line-height:1.3}
.spam{left:156px;top:1069px;width:160px;height:232px}
.spam h3{color:var(--blue)}
.spam svg{display:block;margin:10px auto 0}
.spam-cap{text-align:center;font-size:11.5px;margin-top:4px}
.spam-count{margin:8px auto 0;width:142px;height:50px;border-radius:4px;background:linear-gradient(#f2f2f2,#d9dadc);border:1px solid #c6c7c9;text-align:center;font-size:11.5px;padding-top:6px}
.spam-count b{display:block;color:var(--red);font-size:15px}

.product{width:168px;height:222px;top:674px;background:#fff;border:1px solid var(--grey-line);text-align:center}
.product-head{height:36px;background:linear-gradient(#94cc45,var(--green-dark));color:#fff;font-family:"Montserrat",sans-serif;font-weight:600;font-size:14.5px;line-height:36px}
.price{margin-top:10px;font-size:11px;color:#555}
.price b{font-family:"Montserrat",sans-serif;font-size:24px;color:var(--red);font-weight:700}
.price sup{font-size:15px;color:var(--red);font-weight:700}
.product p{margin-top:8px;font-size:11px;line-height:14px;color:#444;padding:0 8px}
.more{position:absolute;left:34px;bottom:12px;width:100px;height:26px;border-radius:13px;background:linear-gradient(#f4f4f4,#d6d7d9);border:1px solid #bfc0c2;font-family:"Montserrat",sans-serif;font-size:10.5px;font-weight:600;line-height:24px;color:#333}

.intro-h{left:337px;top:918px;font-family:"Montserrat",sans-serif;font-weight:600;font-size:25px;color:#222}
.intro-p{left:337px;top:958px;width:690px;font-size:12px;line-height:18px;color:#444}
.build-h{left:337px;top:1040px;font-family:"Montserrat",sans-serif;font-weight:600;font-size:17px;color:var(--red)}

.builder{left:343px;top:1076px;width:518px;height:448px;background:#f7f7f7;border:1px solid var(--grey-line);padding:20px 18px}
.builder h4{font-family:"Montserrat",sans-serif;font-weight:600;font-size:17px;color:#222}
.os-select{margin-top:14px;width:380px;height:28px;background:linear-gradient(#fff,#e6e6e6);border:1px solid #bbb;border-radius:3px;font-size:12px;line-height:26px;padding-left:10px;position:relative}
.os-select svg{position:absolute;right:10px;top:10px}
.custom{margin-top:20px;font-family:"Montserrat",sans-serif;font-size:12px;font-weight:600;color:var(--red)}
.slider{margin-top:20px}
.slider-label{display:flex;justify-content:space-between;font-size:13px;color:#222;padding:0 0 0 10px}
.slider-label span span{color:#555;font-size:12px}
.track{position:relative;margin-top:10px;height:8px;border-radius:4px;background:#dedfe1;border:1px solid #cfd0d2}
.knob{position:absolute;left:-3px;top:-8px;width:22px;height:22px;border-radius:4px;background:var(--red);display:flex;align-items:center;justify-content:center}

.quote{left:878px;top:1072px;width:162px;height:341px;padding:16px 14px}
.quote h4{font-family:"Montserrat",sans-serif;font-size:16px;font-weight:400;color:#222;line-height:19px}
.quote p{margin-top:14px;font-family:"Tinos",serif;font-style:italic;font-size:12.5px;line-height:17px;color:#444}
.quote cite{display:block;margin-top:16px;font-style:normal;font-size:10.5px;text-align:center;color:#333}

.monthly{left:383px;top:1533px;width:423px;height:46px;display:flex;border-radius:4px;overflow:hidden;border:1px solid #bbb}
.monthly-price{flex:1;background:linear-gradient(#fff,#e8e8e8);font-family:"Montserrat",sans-serif;font-weight:600;font-size:19px;display:flex;align-items:center;justify-content:center;color:#333}
.monthly-btn{width:154px;background:linear-gradient(#e52b2b,var(--red-dark));color:#fff;font-family:"Montserrat",sans-serif;font-weight:700;font-size:14px;display:flex;align-items:center;justify-content:center;gap:8px}

.why{left:339px;top:1600px;width:518px;height:276px;background:#fff;border:1px solid var(--grey-line);padding:16px 22px}
.why h4{font-family:"Montserrat",sans-serif;font-weight:600;font-size:17px;color:#222;margin-bottom:10px}
.why li{list-style:none;display:flex;align-items:center;gap:12px;font-size:12.5px;height:23px;color:#333}
.register{left:619px;top:1829px;width:248px;height:34px;background:linear-gradient(#2f9be3,#1571c2);color:#fff;font-family:"Montserrat",sans-serif;font-size:12.5px;line-height:34px;text-align:center;clip-path:polygon(6% 0,100% 0,100% 100%,6% 100%,0 50%)}

.partners{left:170px;top:1915px;width:870px;height:58px;display:flex;justify-content:space-between;align-items:center}
.partner{height:40px;border-radius:6px;background:#d4d6d9}

.footer{left:143px;top:2004px;width:916px;height:257px;border:1px solid var(--grey-line);background:#fff}
.fcol{top:2026px;font-size:11px;line-height:17px;color:#444}
.fcol h5{font-family:"Montserrat",sans-serif;font-weight:600;font-size:12.5px;color:#222;margin-bottom:10px}
.fdivider{left:823px;top:2004px;width:1px;height:257px;background:var(--grey-line)}
.social{display:flex;align-items:center;gap:12px;margin-bottom:18px}
.social i{width:30px;height:30px;border-radius:4px;display:block}
.copy{left:844px;top:2214px;font-size:11px;line-height:17px;color:#444}
.copy a{color:var(--blue-dark);text-decoration:none}
</style>
</head>
<body>
<div class="page">

  <header>
    <div class="abs topbar"></div>
    <div class="abs brand"><span class="brand-dot"></span>Nimbo31</div>
    <div class="abs utility"><span>Home</span>|<span>Support</span>|<span>Contact us</span><span class="phone">+1300 55 0199</span></div>
    <div class="abs btn-signup">Sign Up</div>
    <div class="abs btn-login">
      <svg width="12" height="14" viewBox="0 0 12 14"><rect x="1" y="6" width="10" height="8" rx="1" fill="#555"/><path d="M3 6V4a3 3 0 0 1 6 0v2" stroke="#555" stroke-width="1.8" fill="none"/></svg>Login</div>
    <nav class="abs nav"><span>Domains</span><span>Web Hosting</span><span>Virtual Servers</span><span>Dedicated Servers</span><span>Resellers</span><span>About Us</span><span>Support</span></nav>
  </header>

  <section>
    <div class="abs hero"></div>
    <div class="abs hero-clouds" role="img" aria-label="Soft white clouds along the bottom of the banner"></div>
    <div class="abs hero-servers" role="img" aria-label="Two server towers standing on a stack of silver discs in a cloud"></div>
    <h1 class="abs hero-title">Simple Cloud Hosting</h1>
    <p class="abs hero-sub">Lorem ipsum dolor sit amet, consectetur adipisicing elit,</p>
  </section>

  <section>
    <div class="abs search"></div>
    <div class="abs search-label">Domain Name Search</div>
    <div class="abs search-input">WWW.</div>
    <div class="abs search-tld">.com.au
      <svg width="10" height="6" viewBox="0 0 10 6" style="margin-left:22px"><path d="M0 0h10L5 6z" fill="#1a7ccf"/></svg></div>
    <div class="abs search-btn">Check Domain</div>
  </section>

  <main>
    <div class="abs main"></div>

    <aside class="abs sidebox aus">
      <h3>100% Australian</h3>
      <div class="aus-map" role="img" aria-label="Map of Australia with the national flag"></div>
      <div class="perk">30 day money-back guarantee</div>
      <div class="perk">24x7 Emergency Phone Support</div>
      <div class="perk">99.9% Service Level Agreement</div>
      <div class="perk">Australia's largest provider of VPS Servers</div>
    </aside>

    <aside class="abs sidebox spam">
      <h3>Spam Filtering</h3>
      <svg width="104" height="104" viewBox="0 0 104 104">
        <circle cx="52" cy="52" r="50" fill="#1e7fcf"/>
        <path d="M52 52 L99 70 A50 50 0 0 1 80 93 Z" fill="#d81e1e"/>
      </svg>
      <p class="spam-cap">Todays Spam vs Email</p>
      <div class="spam-count"><b>153,074</b>Spam blocked today</div>
    </aside>

    <article class="abs product" style="left:331px">
      <div class="product-head">Domain Names</div>
      <div class="price">from <b><sup>$</sup>14.95</b> /year</div>
      <p>Register your domains for .com.au, .net.au, .org.au, .co.nz, .net.nz, .com, .net, .org and many more</p>
      <div class="more">MORE INFO</div>
    </article>
    <article class="abs product" style="left:514px">
      <div class="product-head">Web Hosting</div>
      <div class="price">from <b><sup>$</sup>6.95</b> /month</div>
      <p>Reseller Web Hosting<br>Winsys Website Hosting<br>Lintra Website Hosting<br>FREE Application Vault<br>FREE Email/Webmail</p>
      <div class="more">MORE INFO</div>
    </article>
    <article class="abs product" style="left:695px">
      <div class="product-head">VPS Hosting</div>
      <div class="price">from <b><sup>$</sup>9.95</b> /month</div>
      <p>Contavo VPS<br>Hyperlane VPS<br>Kelp VPS<br>Vesselware VPS<br>Panelo &amp; HostDeck</p>
      <div class="more">MORE INFO</div>
    </article>
    <article class="abs product" style="left:878px">
      <div class="product-head">Dedicated Servers</div>
      <div class="price">from <b><sup>$</sup>99.95</b> /month</div>
      <p>Delmar &amp; Supraform Servers<br>Value-Series Servers<br>Same Day Servers<br>Hourly Backup<br>SERVER SPECIALS</p>
      <div class="more">MORE INFO</div>
    </article>

    <h2 class="abs intro-h">Australian Web Hosting, VPS &amp; Dedicated Servers</h2>
    <p class="abs intro-p">Lorem ipsum dolor sit amet, consectetur adipisicing elit, sed do eiusmod tempor incididunt ut labore et dolore magna aliqua. Ut enim ad minim veniam, quis nostrud exercitation ullamco laboris nisi ut aliquip ex ea commodo consequat. Duis aute irure dolor in reprehenderit in voluptate velit esse cillum dolore eu fugiat nulla pariatur. Excepteur sint occaecat cupidatat non proident, sunt in culpa qui officia deserunt mollit anim id est laborum.</p>
    <h3 class="abs build-h">Build Your Server</h3>

    <section class="abs builder">
      <h4>Select your Operating System</h4>
      <div class="os-select">Centra 4<svg width="10" height="6" viewBox="0 0 10 6"><path d="M0 0h10L5 6z" fill="#444"/></svg></div>
      <div class="custom">Customise your System</div>

      <div class="slider"><div class="slider-label"><span>CPU cores <span>($15.00 per Core)</span></span><span>1 Cores</span></div>
        <div class="track"><div class="knob"><svg width="8" height="10" viewBox="0 0 8 10"><path d="M0 0l8 5-8 5z" fill="#fff"/></svg></div></div></div>
      <div class="slider"><div class="slider-label"><span>Disk Space <span>($0.60 per GB)</span></span><span>25 GB</span></div>
        <div class="track"><div class="knob"><svg width="8" height="10" viewBox="0 0 8 10"><path d="M0 0l8 5-8 5z" fill="#fff"/></svg></div></div></div>
      <div class="slider"><div class="slider-label"><span>Dedicated RAM <span>($15.00 per GB)</span></span><span>.5 GB</span></div>
        <div class="track"><div class="knob"><svg width="8" height="10" viewBox="0 0 8 10"><path d="M0 0l8 5-8 5z" fill="#fff"/></svg></div></div></div>
      <div class="slider"><div class="slider-label"><span>Premium Bandwith <span>($0.70 per GB)</span></span><span>50 GB</span></div>
        <div class="track"><div class="knob"><svg width="8" height="10" viewBox="0 0 8 10"><path d="M0 0l8 5-8 5z" fill="#fff"/></svg></div></div></div>
      <div class="slider"><div class="slider-label"><span>IP Addresses <span>($3.50 per IP Address)</span></span><span>1 IP</span></div>
        <div class="track"><div class="knob"><svg width="8" height="10" viewBox="0 0 8 10"><path d="M0 0l8 5-8 5z" fill="#fff"/></svg></div></div></div>
    </section>

    <aside class="abs sidebox quote">
      <h4>What our Customers Say...</h4>
      <p>Lorem ipsum dolor sit amet, consectetur adipisicing elit, sed do eiusmod tempor incididunt ut labore et dolore magna aliqua. Ut enim ad minim veniam, quis nostrud exercitation.</p>
      <cite>Dana Morrow<br>IT Pty Ltd</cite>
    </aside>

    <div class="abs monthly">
      <div class="monthly-price">Monthly Price: $18.50</div>
      <div class="monthly-btn">Select Software<svg width="12" height="22" viewBox="0 0 12 22"><path d="M2 2l8 9-8 9" stroke="#fff" stroke-width="3.5" fill="none"/></svg></div>
    </div>

    <section class="abs why">
      <h4>Why Choose Nimbo31 for your domain names?</h4>
      <ul>
        <li><svg width="14" height="12" viewBox="0 0 14 12"><path d="M1 6l4 4 8-9" stroke="#5aa52a" stroke-width="2.6" fill="none"/></svg>Duis placerat eros ut metus suscipit non ultricies blandit.</li>
        <li><svg width="14" height="12" viewBox="0 0 14 12"><path d="M1 6l4 4 8-9" stroke="#5aa52a" stroke-width="2.6" fill="none"/></svg>Nunc elementum lacus in turpis accumsan ut feugiat.</li>
        <li><svg width="14" height="12" viewBox="0 0 14 12"><path d="M1 6l4 4 8-9" stroke="#5aa52a" stroke-width="2.6" fill="none"/></svg>Ut vitae velit id nisi dictum fermentum et nec arcu.</li>
        <li><svg width="14" height="12" viewBox="0 0 14 12"><path d="M1 6l4 4 8-9" stroke="#5aa52a" stroke-width="2.6" fill="none"/></svg>Mauris vitae est at odio sollicitudin ultrices blandit eget.</li>
        <li><svg width="14" height="12" viewBox="0 0 14 12"><path d="M1 6l4 4 8-9" stroke="#5aa52a" stroke-width="2.6" fill="none"/></svg>Morbi id risus ac nulla vehicula commodo nec eget lorem.</li>
        <li><svg width="14" height="12" viewBox="0 0 14 12"><path d="M1 6l4 4 8-9" stroke="#5aa52a" stroke-width="2.6" fill="none"/></svg>Duis placerat eros ut metus suscipit non ultricies blandit.</li>
        <li><svg width="14" height="12" viewBox="0 0 14 12"><path d="M1 6l4 4 8-9" stroke="#5aa52a" stroke-width="2.6" fill="none"/></svg>Nunc elementum lacus in turpis accumsan ut feugiat.</li>
        <li><svg width="14" height="12" viewBox="0 0 14 12"><path d="M1 6l4 4 8-9" stroke="#5aa52a" stroke-width="2.6" fill="none"/></svg>Ut vitae velit id nisi dictum fermentum et nec arcu.</li>
      </ul>
    </section>
    <div class="abs register">REGISTER YOUR DOMAIN HERE</div>
  </main>

  <div class="abs partners" aria-label="Technology partners">
    <span class="partner" style="width:72px;border-radius:36px"></span>
    <span class="partner" style="width:60px"></span>
    <span class="partner" style="width:104px"></span>
    <span class="partner" style="width:80px;height:56px"></span>
    <span class="partner" style="width:144px"></span>
    <span class="partner" style="width:90px"></span>
  </div>

  <footer>
    <div class="abs footer"></div>
    <div class="abs fdivider"></div>
    <div class="abs fcol" style="left:166px"><h5>Web Hosting</h5>Winsys or Lintra?<br>Lintra Hosting<br>Winsys Hosting<br>SSL Certificates<br>Advanced WebMail<br>Active Spam Filtering<br>Hosting Control Panel<br>Application Vault</div>
    <div class="abs fcol" style="left:324px"><h5>VPS Virtual Servers</h5>Lintra VPS<br>Winsys VPS<br>Winsys Panelo VPS<br>Lintra Panelo VPS<br>Panelo Hosting VPS<br>HostDeck Virtual Servers<br>Fastico Add-on<br>HostDeck VPS<br>Kelp VPS<br>Hyperlane VPS</div>
    <div class="abs fcol" style="left:486px"><h5>Dedicated Servers</h5>Special Offers<br>Same-Day Dedicated<br>Small Business Servers<br>Medium Business Servers<br>Enterprise Servers<br>Winsys Dedicated Servers<br>Backup and Recovery<br>Data Center<br>Remote Access / Reboot<br>Dedicated Server FAQ<br>Request a Quote</div>
    <div class="abs fcol" style="left:676px"><h5>About Nimbo31</h5>About Nimbo31<br>Partners<br>Terms of Service<br>Service Level Agreement<br>Privacy Policy<br>Refund Policy<br>Jobs @ Nimbo31<br>Contact Us</div>
    <div class="abs fcol" style="left:844px"><h5>Let's Be Social!</h5>
      <div class="social"><i style="background:#3fb2e8"></i>Follow us on Chirpline</div>
      <div class="social"><i style="background:#3b5b9a"></i>Become a fan on Pagebook</div>
    </div>
    <div class="abs copy">© 2012 Nimbo31. All rights reserved.<br><a href="#">Privacy</a> | <a href="#">Sitemap</a></div>
  </footer>

</div>
</body>
</html>
```